English and Spanish Language School Needs a Business Card

Need a business card design a startup company called Maribel Language School. The company will offer English and Spanish conversational level courses designed to make the learner feel comfortable with grammar and vocabulary. We would like to see a logo with some colour that should communicate learning, growth.

Target Market(s)

Consumers and businesses

Industry/Entity Type

Education

Contact Information for Business Card

TBD

Font styles to use
Serif

Requirements
Must have
• Include the following
• Logo
• Name
• Title
• Cellphone Number
• Office Phone number
• Email address
• Office Address

```html
<!DOCTYPE html>
<html lang="en">
<head>
<meta charset="utf-8">
<title>Maribel Language School – Business Card</title>
<link rel="stylesheet" href="https://fonts.googleapis.com/css2?family=Open+Sans:wght@400;600;700&display=swap">
<style>
  :root {
    --brand-red: #c62127;
    --brand-teal: #1a9ea8;
    --ink: #333333;
    --card-white: #ffffff;
    --rule: #e7a0a4;
    --backdrop-top: #262626;
    --backdrop-bottom: #000000;
  }
  * { margin: 0; padding: 0; box-sizing: border-box; }
  html, body { width: 1200px; height: 900px; overflow: hidden; }
  body {
    position: relative;
    background: linear-gradient(180deg, var(--backdrop-top) 0%, #141414 55%, var(--backdrop-bottom) 100%);
    font-family: "Open Sans", Arial, sans-serif;
    color: var(--ink);
  }
  .card {
    position: absolute;
    top: 306px;
    width: 440px;
    height: 271px;
    border-radius: 12px;
  }
  .card-front { left: 149px; background: var(--card-white); }
  .card-back { left: 608px; width: 441px; background: var(--brand-red); }

  .brand-name {
    position: absolute;
    left: 0; right: 0;
    text-align: center;
    font-weight: 700;
    font-size: 27px;
    letter-spacing: -0.3px;
  }
  .card-front .brand-name { top: 62px; color: var(--brand-red); }
  .card-back .brand-name { top: 118px; color: var(--card-white); font-size: 30px; }

  .address {
    position: absolute;
    left: 29px; top: 151px;
    font-size: 12px;
    line-height: 16px;
  }
  .holder {
    position: absolute;
    right: 33px; top: 168px;
    font-size: 14px;
    font-weight: 700;
  }
  .holder .first { color: var(--brand-red); }
  .holder .last { color: var(--brand-teal); }
  .rule {
    position: absolute;
    left: 32px; right: 33px; top: 188px;
    height: 1px;
    background: var(--rule);
  }
  .title {
    position: absolute;
    right: 33px; top: 192px;
    font-size: 12px;
  }
  .contacts {
    position: absolute;
    left: 29px; top: 199px;
    list-style: none;
    font-size: 12px;
    line-height: 16px;
  }
  .contacts li { display: flex; align-items: center; gap: 7px; }
  .contacts svg { width: 9px; height: 9px; fill: var(--brand-red); flex: none; }
</style>
</head>
<body>
  <section class="card card-front" aria-label="Business card front">
    <div class="brand-name">Maribel Language School</div>
    <p class="address">12345, Address Goes Here<br>Country Name, 123456.</p>
    <p class="holder"><span class="first">Daniel</span> <span class="last">Carter</span></p>
    <div class="rule"></div>
    <p class="title">Managing Director</p>
    <ul class="contacts">
      <li>
        <svg viewBox="0 0 10 10" aria-hidden="true"><path d="M2.2 0.5 L3.8 2.4 L3 3.4 Q4 5.6 6.6 7 L7.6 6.2 L9.5 7.8 L8.3 9.5 Q4.5 9.3 2.2 6.8 Q0.4 4.8 0.5 1.7 Z"/></svg>
        044-555 018 274
      </li>
      <li>
        <svg viewBox="0 0 10 10" aria-hidden="true"><path d="M2.5 0 H7.5 V10 H2.5 Z M3.4 1.2 V7.6 H6.6 V1.2 Z M4.4 8.3 H5.6 V9.2 H4.4 Z"/></svg>
        info@maribelschool.com
      </li>
      <li>
        <svg viewBox="0 0 10 10" aria-hidden="true"><path d="M0.5 2 H9.5 V8.5 H0.5 Z M1.2 2.6 L5 5.4 L8.8 2.6 Z" fill-rule="evenodd"/></svg>
        www.maribelschool.com
      </li>
    </ul>
  </section>

  <section class="card card-back" aria-label="Business card back">
    <div class="brand-name">Maribel Language School</div>
  </section>
</body>
</html>
```